Oil and Gas Exploration and Production company needs a business card design

We need a business card design using our logo and colors in the logo. We want a mainstream design.

```html
<!DOCTYPE html>
<html lang="en">
<head>
<meta charset="utf-8">
<title>Norta Energy – Business Card</title>
<link rel="stylesheet" href="https://fonts.googleapis.com/css2?family=Roboto+Slab:wght@400;700;800&display=swap">
<style>
  :root {
    --bg: #e9e6e1;
    --card: #ffffff;
    --ink: #141414;
    --ink-soft: #3a3a3a;
    --gold: #c9962e;
    --rule: #2a2a2a;
  }
  * { margin: 0; padding: 0; box-sizing: border-box; }
  html, body { width: 1200px; height: 911px; overflow: hidden; background: var(--bg); }
  body { position: relative; font-family: "Roboto Slab", Georgia, serif; color: var(--ink); }

  .card {
    position: absolute;
    width: 540px;
    height: 310px;
    background: var(--card);
    border-radius: 18px;
    box-shadow: 0 6px 18px rgba(0,0,0,0.12);
  }
  .card--front { left: 50px; top: 140px; }
  .card--back  { left: 610px; top: 460px; }

  /* Front */
  .holder {
    position: absolute;
    left: 60px; top: 128px;
    width: 200px;
  }
  .holder__name {
    font-weight: 700;
    font-size: 23px;
    letter-spacing: 0.3px;
    color: var(--ink);
    white-space: nowrap;
  }
  .holder__title {
    font-size: 14px;
    color: var(--gold);
    letter-spacing: 0.5px;
    margin-top: 2px;
  }
  .divider {
    position: absolute;
    left: 275px; top: 60px;
    width: 1px; height: 190px;
    background: var(--rule);
  }
  .divider__accent {
    position: absolute;
    left: -1.5px; top: 72px;
    width: 4px; height: 46px;
    background: var(--gold);
  }
  .contact {
    position: absolute;
    left: 302px; top: 78px;
    font-size: 13px;
    line-height: 19px;
    color: var(--ink-soft);
    white-space: nowrap;
  }
  .contact__address { margin-bottom: 6px; }
  .contact__list { list-style: none; }
  .contact__item { display: flex; align-items: center; gap: 8px; height: 21px; }
  .contact__icon { width: 15px; height: 15px; flex: none; }

  /* Back */
  .brand {
    position: absolute;
    inset: 0;
    display: flex;
    align-items: center;
    justify-content: center;
    gap: 14px;
  }
  .brand__dot {
    width: 30px; height: 30px;
    border-radius: 50%;
    background: var(--ink);
  }
  .brand__name {
    font-weight: 800;
    font-size: 48px;
    color: var(--ink);
    letter-spacing: 0.5px;
    white-space: nowrap;
  }
</style>
</head>
<body>

<section class="card card--front" aria-label="Business card front">
  <div class="holder">
    <p class="holder__name">DANIEL REYES</p>
    <p class="holder__title">CEO/FOUNDER</p>
  </div>

  <div class="divider"><span class="divider__accent"></span></div>

  <div class="contact">
    <p class="contact__address">412 Harbor Ridge Road<br>Marlow Falls, Westvale 20418</p>
    <ul class="contact__list">
      <li class="contact__item">
        <svg class="contact__icon" viewBox="0 0 16 16" aria-hidden="true"><circle cx="8" cy="8" r="8" fill="#141414"/><path d="M5.2 4.5l1.4-.3.8 1.8-.9.7c.4.9 1 1.5 1.9 1.9l.7-.9 1.8.8-.3 1.4c-3 .2-5.6-2.4-5.4-5.4z" fill="#c9962e"/></svg>
        <span>555 014 2230</span>
      </li>
      <li class="contact__item">
        <svg class="contact__icon" viewBox="0 0 16 16" aria-hidden="true"><circle cx="8" cy="8" r="8" fill="#141414"/><rect x="5.5" y="3.8" width="5" height="8.4" rx="1" fill="#c9962e"/><rect x="6.4" y="5" width="3.2" height="5" fill="#141414"/></svg>
        <span>555 018 4471</span>
      </li>
      <li class="contact__item">
        <svg class="contact__icon" viewBox="0 0 16 16" aria-hidden="true"><circle cx="8" cy="8" r="8" fill="#141414"/><rect x="4.5" y="6.5" width="7" height="4.5" fill="#c9962e"/><rect x="5.8" y="4.2" width="4.4" height="2.8" fill="#c9962e"/></svg>
        <span>555 012 9086</span>
      </li>
      <li class="contact__item">
        <svg class="contact__icon" viewBox="0 0 16 16" aria-hidden="true"><circle cx="8" cy="8" r="8" fill="#141414"/><rect x="4" y="5" width="8" height="6" fill="#c9962e"/><path d="M4 5l4 3.2L12 5" stroke="#141414" stroke-width="1" fill="none"/></svg>
        <span>info@nortaenergy.com</span>
      </li>
      <li class="contact__item">
        <svg class="contact__icon" viewBox="0 0 16 16" aria-hidden="true"><circle cx="8" cy="8" r="8" fill="#141414"/><circle cx="8" cy="8" r="4" fill="none" stroke="#c9962e" stroke-width="1.2"/><path d="M4 8h8M8 4c-1.5 2.5-1.5 5.5 0 8M8 4c1.5 2.5 1.5 5.5 0 8" stroke="#c9962e" stroke-width="0.9" fill="none"/></svg>
        <span>www.nortaenergy.com</span>
      </li>
    </ul>
  </div>
</section>

<section class="card card--back" aria-label="Business card back">
  <div class="brand">
    <span class="brand__dot" aria-hidden="true"></span>
    <span class="brand__name">Norta Energy</span>
  </div>
</section>

</body>
</html>
```